Larkmoor Drones Business Card

We are a new company based in Central Queensland, Australia that uses specalised drones (Voskel Ferra Q80) to undertake mainly agricultural operations, like spraying weeds, spraying crops, spreading seed etc. I have attached a Plimbo proof of a card I was thinking along the lines of - purely a start point. The drone used in the business card MUST be a Voskel Ferra Q80.
I am very open to other ideas, especially fonts and layout. I don't have website etc set up yet.
The images are stock and easily interchangeable, I just ask that any background images reflect the local central Queensland area. The photo of the drone is not even complete (propellers cut off) and I need a new stock photo – I’m not sure if this is an issue, or I can pay for an image if need be. PLEASE FIND AN FERRA Q80 image - 4 sprayers, not 6.
The logo/business name is very draft and looking for further ideas, ideally incorporating drones or agriculture design elements into the design of the business name. The business name needs work on the graphic/design – it is a draft that I have included, the drone propellers (being a different colour) are DRAFT only and intended for changes. PLEASE DO NOT USE THE DRONE PORPELLER I HAVE USED AS A DRAFT. TRY TO FIND SOMETHING ELSE.. The arrow is a shape and not aligned in any way, I would also like ideas on different fonts and additional elements, like air streams, aviation elements, aviation or country western (farming like) themes and fonts etc.
Ideally looking at staying within the blue, green and yellow colours, keeping with an natural, outdoorsy, environmental feel.

Target Market(s)

Farmers, Agriculture, Local Governments, Land Managers

Industry/Entity Type

Agriculture, Drones, Aviation

Contact Information for Business Card

Agricultural Drone (Voskel Ferra Q80), Farming, Business Name.

Font styles to use
Sans Serif

Colors
0054AA
0677BA
7BADD7
CADEEF
E8F1F8
0094D4
00A9DD
6FCCEA
C7EBF8
E9F6FB
00AB8E
00BBA5
67D7C9
C6EFE9
E9F9F6
59FF00
82FF00
B8FF75
E3FFCB
F4FFEA

Requirements
Must have
• Voskel Ferra Q80 Drone
Should not have
• Tractors

```html
<!DOCTYPE html>
<html lang="en">
<head>
<meta charset="utf-8">
<title>Larkmoor Drones Business Card</title>
<link rel="stylesheet" href="https://fonts.googleapis.com/css2?family=Alfa+Slab+One&family=Archivo+Black&family=Cinzel:wght@400&family=Russo+One&family=Roboto+Slab:wght@700&display=swap">
<style>
  :root {
    --stage: #2a2a2a;
    --brand-blue: #2340a0;
    --field-green: #7f9a3e;
    --field-green-dark: #6a8430;
    --sun-orange: #e9a45a;
    --sun-gold: #f4c26b;
    --swoosh-tan: #e6a877;
    --white: #ffffff;
  }
  * { box-sizing: border-box; margin: 0; padding: 0; }
  html, body { width: 1200px; height: 800px; overflow: hidden; background: var(--stage); }
  .stage {
    width: 1200px; height: 800px;
    display: flex; align-items: center; justify-content: center; gap: 40px;
  }
  .card {
    position: relative; width: 560px; height: 320px;
    border-radius: 28px; overflow: hidden;
    background: var(--field-green);
    box-shadow: 0 14px 30px rgba(0,0,0,.5);
  }
  .card-art { position: absolute; inset: 0; width: 100%; height: 100%; }

  /* Front */
  .service-line {
    position: absolute; top: 26px; left: 0; right: 0; text-align: center;
    font-family: "Alfa Slab One", serif; font-size: 27px; letter-spacing: 3px;
    color: var(--brand-blue);
  }
  .front-name-top {
    position: absolute; left: 0; right: 0; top: 188px; height: 48px;
    display: flex; align-items: center; justify-content: center;
    font-family: "Archivo Black", sans-serif; font-size: 34px; line-height: 1;
    color: var(--white); letter-spacing: 1px;
  }
  .front-name-bottom {
    position: absolute; left: 0; right: 0; top: 242px; text-align: center;
    font-family: "Archivo Black", sans-serif; font-size: 34px; line-height: 1;
    color: var(--brand-blue); letter-spacing: 1px;
  }
  .front-tagline {
    position: absolute; left: 0; right: 0; top: 284px; text-align: center;
    font-family: "Cinzel", serif; font-size: 12px; color: var(--white);
    letter-spacing: 1.5px;
  }

  /* Back */
  .offer {
    position: absolute; left: 28px; top: 92px; width: 220px;
    font-family: "Russo One", sans-serif; font-size: 16px; line-height: 1.3;
    color: var(--white); text-transform: uppercase;
  }
  .contact-list {
    position: absolute; right: 26px; top: 110px; list-style: none;
    font-family: "Roboto Slab", serif; font-size: 13px; color: var(--white);
  }
  .contact-list li {
    display: flex; align-items: center; justify-content: flex-end; gap: 8px;
    height: 23px;
  }
  .contact-icon {
    width: 18px; height: 18px; border-radius: 50%; background: var(--white);
    display: flex; align-items: center; justify-content: center; flex: none;
  }
  .contact-icon svg { width: 11px; height: 11px; }
  .back-logo { position: absolute; left: 0; right: 0; top: 248px; text-align: center; }
  .back-name {
    font-family: "Archivo Black", sans-serif; font-size: 30px; line-height: 1;
    letter-spacing: 1px; white-space: nowrap;
  }
  .back-name .name-first { color: var(--white); }
  .back-name .name-second { color: var(--brand-blue); }
  .back-tagline {
    font-family: "Cinzel", serif; font-size: 12px; color: var(--white);
    letter-spacing: 1.5px; margin-top: 6px;
  }
</style>
</head>
<body>
<main class="stage">

  <!-- Front of card -->
  <section class="card card-front">
    <svg class="card-art" viewBox="0 0 560 320" preserveAspectRatio="none">
      <defs>
        <linearGradient id="frontPhoto" x1="0" y1="0" x2="0" y2="1">
          <stop offset="0" stop-color="#e08a45"/>
          <stop offset=".35" stop-color="#f4c26b"/>
          <stop offset=".7" stop-color="#b7ae6a"/>
          <stop offset="1" stop-color="#8a9c4a"/>
        </linearGradient>
      </defs>
      <rect x="0" y="0" width="560" height="190" fill="url(#frontPhoto)" role="img"
            aria-label="Photo: Voskel Ferra Q80 spray drone with four nozzles over a Central Queensland crop at sunset"/>
      <rect x="0" y="188" width="560" height="48" fill="var(--brand-blue)"/>
      <rect x="0" y="236" width="560" height="84" fill="var(--field-green)"/>
    </svg>
    <p class="service-line">SPRAY · WEED · SEED · FEED</p>
    <p class="front-name-top">LARKMOOR</p>
    <p class="front-name-bottom">DRONES</p>
    <p class="front-tagline">SERVICING CENTRAL QUEENSLAND</p>
  </section>

  <!-- Back of card -->
  <section class="card card-back">
    <svg class="card-art" viewBox="0 0 560 320" preserveAspectRatio="none">
      <defs>
        <linearGradient id="backPhoto" x1="0" y1="0" x2="0" y2="1">
          <stop offset="0" stop-color="#f0a85a"/>
          <stop offset=".4" stop-color="#f6cf84"/>
          <stop offset=".75" stop-color="#a9ad66"/>
          <stop offset="1" stop-color="#7f9a3e"/>
        </linearGradient>
        <linearGradient id="offerPanel" x1="0" y1="0" x2="1" y2="0">
          <stop offset="0" stop-color="#2340a0"/>
          <stop offset="1" stop-color="#4a6a7a"/>
        </linearGradient>
        <linearGradient id="fieldFade" x1="0" y1="0" x2="0" y2="1">
          <stop offset="0" stop-color="#7f9a3e" stop-opacity="0"/>
          <stop offset="1" stop-color="#7f9a3e"/>
        </linearGradient>
      </defs>
      <rect x="0" y="0" width="560" height="320" fill="url(#backPhoto)" role="img"
            aria-label="Photo: Voskel Ferra Q80 drone spraying a Central Queensland paddock at sunrise"/>
      <rect x="0" y="180" width="560" height="140" fill="url(#fieldFade)"/>
      <path d="M0 0 H250 C230 120 170 190 0 230 Z" fill="var(--field-green)"/>
      <path d="M0 60 H300 C250 110 190 190 0 230 Z" fill="url(#offerPanel)"/>
      <path d="M0 236 C150 205 250 170 310 40 C330 15 380 5 430 0"
            fill="none" stroke="var(--swoosh-tan)" stroke-width="5"/>
      <path d="M300 150 C330 80 370 30 420 0 L440 0 C390 35 345 90 305 158 Z"
            fill="var(--brand-blue)"/>
    </svg>
    <p class="offer">Agricultural Drone (Voskel Ferra Q80), Farming</p>
    <ul class="contact-list">
      <li>(07) 4900 1583
        <span class="contact-icon"><svg viewBox="0 0 24 24"><path fill="#7f9a3e" d="M6.6 10.8a15 15 0 0 0 6.6 6.6l2.2-2.2a1 1 0 0 1 1-.25 11 11 0 0 0 3.6.6 1 1 0 0 1 1 1V20a1 1 0 0 1-1 1A17 17 0 0 1 3 4a1 1 0 0 1 1-1h3.5a1 1 0 0 1 1 1c0 1.25.2 2.45.6 3.6a1 1 0 0 1-.25 1z"/></svg></span></li>
      <li>www.larkmoordrones.au
        <span class="contact-icon"><svg viewBox="0 0 24 24"><g fill="none" stroke="#7f9a3e" stroke-width="2"><circle cx="12" cy="12" r="9"/><path d="M3 12h18M12 3c3 3 3 15 0 18M12 3c-3 3-3 15 0 18"/></g></svg></span></li>
      <li>info@larkmoordrones.au
        <span class="contact-icon"><svg viewBox="0 0 24 24"><g fill="none" stroke="#7f9a3e" stroke-width="2"><rect x="3" y="5" width="18" height="14" rx="1"/><path d="M3 6l9 7 9-7"/></g></svg></span></li>
      <li>@larkmoordrones <span class="contact-icon"></span></li>
      <li>@larkmoordrones <span class="contact-icon"></span></li>
    </ul>
    <div class="back-logo">
      <p class="back-name"><span class="name-first">LARKMOOR</span> <span class="name-second">DRONES</span></p>
      <p class="back-tagline">SERVICING CENTRAL QUEENSLAND</p>
    </div>
  </section>

</main>
</body>
</html>
```